New Fitness Company looking for creative website design

I am building a new fitness matching service. To match customers looking for fitness services to professionals that meet their requirements

My business will have 5 different divisions and I would like to have tabs for each division

1. Matching client to trainer - I need to have video upload capability on the site
2. Corporate personal training services

-The site needs a shopping cart as well as payment capability.
- I am looking for the site to be bright and inviting as well as have clients and trainers going through some type of workout on the main page.
- I also need the capability to capture email addresses
- We are going to have a section that ask the customer questions to match up the trainer so that needs to be a part of the site
-Ability to have trainers rated in a 1 star to 5 stars as well as reviews
- Site should be inviting, bright and vibrant colors that catch the eye and is easy to use
- Similar sites for inspiration are www.zavrello.com where you give a description of how the service works, short video and various services.

Target Market(s)

mid income to high income, mix of female and male customers

Industry/Entity Type

Fitness

Coding

Coded - Design and coding required

Number of Pages Required

5+ page

Font styles to use
Serif
Sans Serif

Requirements
Must have
• Must have the logos that I provided in the website
Should not have
• Not looking for bodybuilders on website. This is for everyday people that are interested in staying in shape and working out. So active fit people will resonate with my prospects

```html
<!DOCTYPE html>
<html lang="en">
<head>
<meta charset="utf-8">
<title>Kestrel Fitness</title>
<link rel="stylesheet" href="https://fonts.googleapis.com/css2?family=Poiret+One&family=Open+Sans:wght@400;600;700&display=swap">
<style>
:root{
  --green:#3db349;
  --green-dark:#2f9a3b;
  --orange:#ee8c1d;
  --orange-dark:#d9741a;
  --ink:#222;
  --text:#666;
  --topbar:#1c241e;
  --footer:#1f1f1f;
  --white:#fff;
  --line:#e6e6e6;
}
*{margin:0;padding:0;box-sizing:border-box}
html,body{width:1200px;height:2476px;overflow:hidden;background:var(--white)}
body{position:relative;font-family:"Open Sans",Arial,sans-serif;color:var(--text)}
.abs{position:absolute}
.topbar{left:0;top:0;width:1200px;height:32px;background:var(--topbar);color:#fff;font-size:10px;font-weight:600;text-transform:uppercase}
.topbar a{position:absolute;top:0;height:32px;line-height:32px;padding:0 16px;color:#fff;text-decoration:none;border-left:1px solid #333;border-right:1px solid #333;display:flex;align-items:center;gap:6px}
.header{left:0;top:32px;width:1200px;height:163px}
.follow{left:98px;top:72px;display:flex;align-items:center;gap:8px;font-size:10px;font-weight:700;color:var(--orange)}
.social{width:26px;height:26px;border-radius:50%;display:inline-block}
.brand{left:460px;top:50px;width:280px;text-align:center}
.brand-mark{display:block;width:22px;height:22px;border-radius:50%;background:var(--green);margin:0 auto 10px}
.brand-name{font-family:"Open Sans",sans-serif;font-weight:700;font-size:34px;color:var(--green);letter-spacing:1px;line-height:1;text-transform:uppercase}
.search{left:860px;top:65px;width:240px;height:34px;display:flex}
.search input{flex:1;border:1px solid #ddd;font-size:10px;padding:0 12px;color:#999;font-family:inherit}
.search button{width:38px;border:0;background:var(--orange)}
.nav{left:0;top:195px;width:1200px;height:56px;background:linear-gradient(var(--green),var(--green-dark))}
.nav ul{list-style:none;display:flex;position:absolute;left:98px;top:0;height:56px}
.nav li{height:56px;line-height:56px;font-size:11px;font-weight:700;color:#fff;text-transform:uppercase;text-align:center}
.nav li.active{background:#fff;color:var(--green);border-bottom:3px solid var(--green);margin-top:3px;height:50px;line-height:48px}
.hero{left:0;top:251px;width:1200px;height:557px;background:linear-gradient(180deg,#f4f6f4 0%,#eef0ee 68%,#dcc8a8 72%,#c9ab80 100%)}
.hero-photo{left:410px;top:0;width:740px;height:557px;background:radial-gradient(ellipse at 55% 55%,#e3d2bf 0%,rgba(228,214,196,.6) 35%,rgba(240,240,238,0) 65%)}
.hero-card{left:98px;top:181px;width:387px;height:146px;background:rgba(255,255,255,.92);border-bottom:3px solid var(--orange);box-shadow:0 1px 4px rgba(0,0,0,.15);padding:14px 22px}
.hero-card h1{font-family:"Poiret One",cursive;font-weight:400;font-size:36px;color:var(--ink);line-height:1.2}
.hero-card p{font-size:12px;font-weight:700;color:var(--orange);text-transform:uppercase;margin-top:8px;line-height:1.55}
.btn-shop{display:inline-block;margin-top:10px;background:linear-gradient(var(--orange),var(--orange-dark));color:#fff;font-size:13px;padding:11px 28px;border-radius:2px}
.dots{left:98px;top:416px;display:flex;gap:8px}
.dots span{width:13px;height:13px;border-radius:50%;background:#fff;border:1px solid #ccc}
.dots span.on{background:var(--green);border-color:var(--green)}
.section-title{left:0;width:1200px;text-align:center;font-family:"Poiret One",cursive;font-size:29px;color:var(--green)}
.lead{left:220px;width:760px;text-align:center;font-size:12.5px;line-height:23px}
.video{left:180px;top:987px;width:804px;height:439px;background:linear-gradient(90deg,#c9b8a0 0%,#e9ddd0 30%,#d8b6ae 55%,#e7d8c8 80%,#bfa892 100%);box-shadow:0 18px 14px -14px rgba(0,0,0,.5)}
.play{left:364px;top:172px;width:76px;height:54px;background:rgba(30,30,30,.85);border-radius:6px}
.controls{left:0;bottom:0;width:804px;height:26px;background:#1b1b1b;border-top:3px solid #c4302b;color:#ddd;font-size:10px;display:flex;align-items:center;padding:0 14px;gap:16px}
.caption{left:180px;top:1460px;width:840px;text-align:center;font-size:11px;line-height:20px}
.divider{left:98px;top:1577px;width:1004px;height:1px;background:var(--line)}
.service{top:1707px;width:360px;text-align:center}
.service .icon{width:106px;height:106px;border-radius:50%;margin:0 auto;display:flex;align-items:center;justify-content:center}
.service h3{font-family:"Poiret One",cursive;font-weight:400;font-size:16px;font-weight:700;color:var(--ink);margin-top:22px}
.service p{font-size:11px;line-height:19px;margin:8px auto 0;width:300px}
.vline{top:1807px;width:1px;height:110px;background:var(--line)}
.products{left:0;top:1988px;width:1200px;height:393px;background:linear-gradient(90deg,#2a3326,#4a5741 35%,#3e4b37 65%,#2c3428)}
.products .section-title{color:#fff;top:96px}
.card{top:160px;width:165px;height:144px;border:3px solid #fff;overflow:hidden}
.sale{position:absolute;right:8px;top:6px;width:46px;height:46px;border-radius:50%;background:var(--orange);color:#fff;font-size:12px;line-height:46px;text-align:center}
.card.featured{background:rgba(61,179,73,.85)}
.card.featured .sale{background:rgba(255,255,255,.25)}
.add-cart{position:absolute;left:30px;top:54px;width:100px;height:32px;border:1px solid #fff;border-radius:3px;color:#fff;font-size:10px;display:flex;align-items:center;justify-content:center;gap:5px}
.arrow{top:205px}
.footer{left:0;top:2381px;width:1200px;height:95px;background:var(--footer)}
.footer ul{list-style:none;position:absolute;left:110px;top:24px;width:980px;display:flex;justify-content:space-between;font-size:10px;font-weight:600;color:#ccc;text-transform:uppercase}
.footer li::before{content:"• ";color:#999}
.footer p{position:absolute;left:0;top:65px;width:1200px;text-align:center;font-size:10px;font-weight:600;color:#999;text-transform:uppercase}
</style>
</head>
<body>

<div class="abs topbar">
  <a style="left:100px"><svg width="9" height="10" viewBox="0 0 9 10"><rect x="1" y="4" width="7" height="6" fill="#fff"/><path d="M2.5 4V2.5a2 2 0 0 1 4 0V4" stroke="#fff" fill="none"/></svg>Login</a>
  <a style="left:178px"><svg width="12" height="10" viewBox="0 0 12 10"><circle cx="5" cy="3" r="2.5" fill="#fff"/><path d="M0 10a5 4 0 0 1 10 0z" fill="#fff"/></svg>Sign up</a>
  <a style="left:787px"><svg width="10" height="10" viewBox="0 0 10 10"><path d="M2 0l2 3-1 1.5a6 6 0 0 0 2.5 2.5L7 6l3 2-1 2C4 10 0 6 0 1z" fill="#fff"/></svg>Call us: 555-010-2040</a>
  <a style="left:937px"><svg width="10" height="10" viewBox="0 0 10 10"><path d="M0 0h5l5 5-5 5-5-5z" fill="#fff"/><circle cx="2.5" cy="2.5" r="1" fill="#1c241e"/></svg>Shop your products</a>
</div>

<header class="abs header">
  <div class="abs follow" style="top:40px">FOLLOW WITH US :
    <span class="social" style="background:#3b5998" aria-label="Social profile"></span>
    <span class="social" style="background:#33a1d8" aria-label="Social profile"></span>
    <span class="social" style="background:#333" aria-label="Social profile"></span>
    <span class="social" style="background:#1f77a8" aria-label="Social profile"></span>
  </div>
  <div class="abs brand">
    <span class="brand-mark"></span>
    <div class="brand-name">Kestrel Fitness</div>
  </div>
  <form class="abs search" style="top:66px">
    <input type="text" placeholder="SEARCH">
    <button type="button" aria-label="Search"><svg width="14" height="14" viewBox="0 0 14 14"><circle cx="6" cy="6" r="4" stroke="#fff" stroke-width="2" fill="none"/><path d="M9 9l4 4" stroke="#fff" stroke-width="2"/></svg></button>
  </form>
</header>

<nav class="abs nav">
  <ul>
    <li class="active" style="width:124px">Home</li>
    <li style="width:130px">About us</li>
    <li style="width:100px">Store</li>
    <li style="width:120px">Videos</li>
    <li style="width:136px">Products</li>
    <li style="width:124px">Training</li>
    <li style="width:98px">FAQ</li>
    <li style="width:172px">Contact us</li>
  </ul>
</nav>

<section class="abs hero">
  <div class="abs hero-photo" role="img" aria-label="Woman in white activewear stretching on a wooden studio floor"></div>
  <div class="abs hero-card">
    <h1>Need a Fitness Body..!</h1>
    <p>Sed ut perspiciatis unde omnis iste natus error<br>sit aperiam, eaque ipsa quae ab illo inve...</p>
    <span class="btn-shop">Shop Now!</span>
  </div>
  <div class="abs dots"><span class="on"></span><span></span><span></span></div>
</section>

<h2 class="abs section-title" style="top:858px">Matching Client to Trainer</h2>
<p class="abs lead" style="top:902px">Nemo enim ipsam voluptatem quia voluptas sit aspernatur aut odit aut fugit, sed quia consequuntur magni dolores eos qui ratione voluptatem sequi nesciunt. Neque porro quisquam est, qui dolorem ipsum quia...</p>

<div class="abs video" role="img" aria-label="Video of a client and a trainer chatting over a snack in a gym café">
  <div class="abs play"><svg width="76" height="54" viewBox="0 0 76 54"><path d="M31 17l16 10-16 10z" fill="#fff"/></svg></div>
  <div class="abs controls">
    <svg width="10" height="12"><rect x="1" y="1" width="3" height="10" fill="#ddd"/><rect x="6" y="1" width="3" height="10" fill="#ddd"/></svg>
    <svg width="14" height="12"><path d="M0 4h3l4-3v10l-4-3H0z" fill="#ddd"/></svg>
    <span>0:05 / 0:24</span>
    <span style="margin-left:auto">360p</span>
    <svg width="12" height="12"><path d="M1 1h4M1 1v4M11 11h-4M11 11v-4" stroke="#ddd" stroke-width="2"/></svg>
  </div>
</div>
<p class="abs caption">Accusantium doloremque laudantium, totam rem aperiam, eaque ipsa quae ab veritatis et quasi architecto beatae vitae dicta sunt explicabo. Nemo enim ipsam voluptatem quia voluptas sit aspernatur aut odit aut fugit, sed quia consequuntur magni dolores eos qui ratione voluptatem sequi nesciunt.<br>Neque porro quisquam est...</p>

<div class="abs divider"></div>

<h2 class="abs section-title" style="top:1628px">Our Services</h2>
<div class="abs service" style="left:59px">
  <div class="icon" style="background:var(--orange)"><svg width="40" height="44" viewBox="0 0 40 44" fill="none" stroke="#fff" stroke-width="2"><circle cx="20" cy="6" r="5"/><path d="M4 14h32M14 14v28M26 14v28M14 28h12"/></svg></div>
  <h3>Similique sunt in culpa</h3>
  <p>Nemo enim ipsam voluptatem quia voluptas sit tur aut odit aut fugit, sed quia consequuntur magni dolores eos qui ratione voluptatem sequi nesci...</p>
</div>
<div class="abs vline" style="left:422px"></div>
<div class="abs service" style="left:420px">
  <div class="icon" style="background:var(--green)"><svg width="40" height="40" viewBox="0 0 40 40" fill="none" stroke="#fff" stroke-width="2"><path d="M6 34C6 14 18 6 36 4c-2 18-10 30-30 30z"/><path d="M6 34L24 16"/></svg></div>
  <h3>Similique sunt in culpa</h3>
  <p>Nemo enim ipsam voluptatem quia voluptas sit tur aut odit aut fugit, sed quia consequuntur magni dolores eos qui ratione voluptatem sequi nesci...</p>
</div>
<div class="abs vline" style="left:782px"></div>
<div class="abs service" style="left:780px">
  <div class="icon" style="background:#2b2b2b"><svg width="48" height="40" viewBox="0 0 48 40" fill="none" stroke="#fff" stroke-width="2"><circle cx="24" cy="10" r="6"/><circle cx="10" cy="16" r="5"/><circle cx="38" cy="16" r="5"/><path d="M14 36a10 10 0 0 1 20 0zM2 36a8 8 0 0 1 12-7M46 36a8 8 0 0 0-12-7"/></svg></div>
  <h3>Similique sunt in culpa</h3>
  <p>Nemo enim ipsam voluptatem quia voluptas sit tur aut odit aut fugit, sed quia consequuntur magni dolores eos qui ratione voluptatem sequi nesci...</p>
</div>

<section class="abs products" role="region" aria-label="Our products, over a photo of people exercising outdoors">
  <h2 class="abs section-title">Our Products</h2>
  <svg class="abs arrow" style="left:100px" width="22" height="70" viewBox="0 0 22 70"><path d="M20 2L2 35l18 33" stroke="#ccc" stroke-width="1.5" fill="none"/></svg>
  <svg class="abs arrow" style="left:1078px" width="22" height="70" viewBox="0 0 22 70"><path d="M2 2l18 33L2 68" stroke="#ccc" stroke-width="1.5" fill="none"/></svg>
  <div class="abs card featured" style="left:234px" role="img" aria-label="Green protein shaker product">
    <span class="sale">Sale</span>
    <span class="add-cart"><svg width="10" height="9" viewBox="0 0 10 9"><path d="M0 0h2l1 5h6l1-4H3" stroke="#fff" fill="none"/><circle cx="4" cy="8" r="1" fill="#fff"/><circle cx="8" cy="8" r="1" fill="#fff"/></svg>Add to Cart</span>
  </div>
  <div class="abs card" style="left:422px;background:linear-gradient(160deg,#f3ece1 0%,#e4d3b8 50%,#8c5a3c 100%)" role="img" aria-label="Protein powder in bowls"><span class="sale">Sale</span></div>
  <div class="abs card" style="left:610px;background:linear-gradient(160deg,#f6f1ea 0%,#e7cfa8 50%,#c9343c 100%)" role="img" aria-label="Granola with berries"><span class="sale">Sale</span></div>
  <div class="abs card" style="left:799px;background:linear-gradient(160deg,#efe9e3 0%,#b7a89a 50%,#2a2a2a 100%)" role="img" aria-label="Black shaker bottle and supplements"><span class="sale">Sale</span></div>
</section>

<footer class="abs footer">
  <ul>
    <li>Home</li><li>About us</li><li>Store</li><li>Videos</li><li>Products</li><li>Training</li><li>FAQ</li><li>Contact us</li>
  </ul>
  <p>Copyrights © Kestrel .2015 | Allrights reserved.</p>
</footer>

</body>
</html>
```